Luxury Business Card Design for High-End Window Treatments

Gilded Slatworks
Custom Plantation Shutters & Architectural Shading Systems

⸻

BACK

Daniel Trevick
Owner

Custom Interior & Exterior Window Treatments

919-555-0148
gildedslatworks.com

I have included a picture that I’m hoping we can use on the back, but I’m also wondering if you can get rid of the ladder? Should we get rid of shutters , shades and blinds underneath Gilded Slatworks?

Target Market(s)

High-end residential homeowners, custom home builders, architects, interior designers, and luxury renovation clients seeking premium plantation shutters and motorized architectural shading systems.

Industry/Entity Type

Custom Window treatments

Contact Information for Business Card

Front Gilded Slatworks Custom Plantation Shutters Motorized Architectural Shading Systems BACK Daniel Trevick Owner 919-555-0148 GildedSlatworks.com Custom Interior & Exterior Window Treatments By Appointment

Requirements
Nice to have
• Not 100% sure on nice to halves or the color but you can definitely check out my website to get a better understanding of what I’m trying to do

```html
<!DOCTYPE html>
<html lang="en">
<head>
<meta charset="utf-8">
<title>Gilded Slatworks — Business Card</title>
<link href="https://fonts.googleapis.com/css2?family=Playfair+Display:wght@400;500&family=Arvo:wght@700&family=Poppins:wght@400&display=swap" rel="stylesheet">
<style>
  :root {
    --backdrop: #c9c9c9;
    --card-black: #0a0a0a;
    --gold: #bea94f;
    --white: #ffffff;
    --photo-sky: #2a3450;
    --photo-mid: #4a4f52;
    --photo-green: #3d5230;
  }
  * { margin: 0; padding: 0; box-sizing: border-box; }
  html, body {
    width: 1200px; height: 900px; overflow: hidden;
    background: var(--backdrop);
  }
  .canvas {
    width: 1200px; height: 900px;
    display: flex; flex-direction: column;
    align-items: center; justify-content: center; gap: 50px;
  }
  .card {
    position: relative;
    width: 620px; height: 354px;
    border-radius: 26px;
    background: var(--card-black);
    overflow: hidden;
    box-shadow: 0 8px 18px rgba(0,0,0,0.25);
  }

  /* Front */
  .front-brand {
    position: absolute; top: 28px; left: 0; right: 0; height: 150px;
    display: flex; flex-direction: column; justify-content: center;
    font-family: "Playfair Display", serif;
    font-weight: 400; font-size: 48px; line-height: 1.05; color: var(--gold);
  }
  .front-brand span { display: block; }
  .front-brand .brand-line-1 { padding-left: 250px; }
  .front-brand .brand-line-2 { padding-left: 300px; }
  .front-band {
    position: absolute; left: 0; right: 0; bottom: 0; height: 164px;
    background: var(--gold);
  }
  .front-tagline {
    position: absolute; left: 0; right: 0; top: 206px;
    text-align: center;
    font-family: "Playfair Display", serif;
    font-size: 17px; line-height: 1.3; color: var(--white);
  }

  /* Back */
  .back-photo {
    position: absolute; top: 0; left: 0; width: 620px; height: 354px;
  }
  .back-name {
    position: absolute; left: 34px; top: 136px;
    font-family: "Arvo", serif; font-weight: 700;
    font-size: 27px; color: var(--gold); line-height: 1;
  }
  .back-role {
    position: absolute; left: 36px; top: 167px;
    font-family: "Poppins", sans-serif; font-size: 16px; line-height: 1.2; color: var(--white);
  }
  .back-contact {
    position: absolute; left: 36px; top: 206px;
    list-style: none;
    font-family: "Poppins", sans-serif; font-size: 16px; color: var(--white);
  }
  .back-contact li { display: flex; align-items: center; gap: 10px; height: 24px; }
  .back-contact svg { width: 16px; height: 16px; fill: var(--gold); flex: none; }
  .back-tagline {
    position: absolute; left: 36px; bottom: 22px;
    font-family: "Playfair Display", serif;
    font-size: 15px; line-height: 1.3; color: var(--gold);
  }
</style>
</head>
<body>
<main class="canvas">

  <section class="card card-front" aria-label="Card front">
    <div class="front-brand"><span class="brand-line-1">Gilded</span><span class="brand-line-2">Slatworks</span></div>
    <div class="front-band"></div>
    <p class="front-tagline">Gilded Slatworks Custom<br>Plantation Shutters Motorized<br>Architectural Shading Systems</p>
  </section>

  <section class="card card-back" aria-label="Card back">
    <svg class="back-photo" viewBox="0 0 620 354">
      <defs>
        <linearGradient id="porch-tones" x1="0" y1="0" x2="0" y2="1">
          <stop offset="0" stop-color="#2a3450"/>
          <stop offset="0.55" stop-color="#4a4f52"/>
          <stop offset="1" stop-color="#3d5230"/>
        </linearGradient>
      </defs>
      <circle cx="540" cy="95" r="225" fill="#bea94f"/>
      <circle cx="552" cy="92" r="220" fill="url(#porch-tones)" role="img" aria-label="Photo of a covered home porch with white columns, window shades and landscaped shrubs"/>
    </svg>

    <h2 class="back-name">Daniel Trevick</h2>
    <p class="back-role">Owner</p>
    <ul class="back-contact">
      <li>
        <svg viewBox="0 0 24 24"><path d="M6.6 10.8a15.1 15.1 0 0 0 6.6 6.6l2.2-2.2a1 1 0 0 1 1-.25 11.4 11.4 0 0 0 3.6.57 1 1 0 0 1 1 1V20a1 1 0 0 1-1 1A17 17 0 0 1 3 4a1 1 0 0 1 1-1h3.5a1 1 0 0 1 1 1c0 1.25.2 2.45.57 3.57a1 1 0 0 1-.25 1z"/></svg>
        <span>919-555-0148</span>
      </li>
      <li>
        <svg viewBox="0 0 24 24"><path d="M2 5h20v14H2z M3.5 6.5 12 13l8.5-6.5" fill="#bea94f" stroke="#0a0a0a" stroke-width="1.5"/></svg>
        <span>GildedSlatworks.com</span>
      </li>
    </ul>
    <p class="back-tagline">Custom Interior &amp;<br>Exterior Window<br>Treatments By Appointment</p>
  </section>

</main>
</body>
</html>
```